TL - business card

Tallow Partners is an insurance brokerage firm, inovative, proactive, vigorous, which aims to become the leader of the insurance brokers in Anfrica. We should like to get some designs which should be avoided also in Gray / Metallic for the Administration and Orange / Blue for the Managers (ike in the picture sent). The Blue / Green logo is not the correct one, but the source of the file. Please adjust the color accordingly for the business cards. 1 / Orange / Blue 2 / Gray / Metallic We want something classic but which is transmitted strenght, inovation, modernity and most of all, rapidity. We want something start-up like, very punchy and catching eye remaining profesional at the same time. Name: Dorian Whitlock Function: Managing Director Address: N ° 17/18 Rua Veloso - R / C 2B Direita - Bairro Mutamba - Luanda Tel: (+244) 947 582 316 Email: dorian.whitlock@tallow-p.example Website: www.tallow-p. example We want classic in the front and creative, colorfull at the back. The cards will be printed in relief, with very high quality of paper.
Insurance Broker
Colors
Designer to choose colors to be used in the design.

```html
<!DOCTYPE html>
<html lang="en">
<head>
<meta charset="utf-8">
<title>Tallow Partners – Business Card</title>
<link href="https://fonts.googleapis.com/css2?family=Montserrat:wght@400;500;600;700&display=swap" rel="stylesheet">
<style>
  :root {
    --bg: #141414;
    --card: #262626;
    --card-edge: #2e2e2e;
    --metal: #9a9a9a;
    --accent: #29a3dc;
    --text: #e6e6e6;
  }
  * { box-sizing: border-box; margin: 0; padding: 0; }
  html, body { width: 1200px; height: 900px; overflow: hidden; }
  body {
    background: var(--bg);
    font-family: "Montserrat", Arial, sans-serif;
    position: relative;
  }
  .card {
    position: absolute;
    left: 260px;
    width: 680px;
    height: 388px;
    background: linear-gradient(135deg, var(--card-edge), var(--card) 60%, #202020);
    box-shadow: 0 14px 30px rgba(0,0,0,0.6);
  }
  .card--front { top: 48px; }
  .card--back { top: 464px; }

  .brand {
    display: flex;
    flex-direction: column;
    align-items: center;
    gap: 16px;
  }
  .brand__dot {
    width: 78px;
    height: 78px;
    border-radius: 50%;
  }
  .brand__name {
    font-weight: 700;
    letter-spacing: 1px;
    text-transform: uppercase;
  }
  .card--front .brand {
    position: absolute;
    left: 0; right: 0; top: 108px;
  }
  .card--front .brand__dot { background: var(--metal); }
  .card--front .brand__name { color: var(--metal); font-size: 34px; }

  .card--back .brand {
    position: absolute;
    left: 28px; width: 300px; top: 118px;
  }
  .card--back .brand__dot { background: var(--accent); }
  .card--back .brand__name { color: var(--accent); font-size: 27px; }

  .divider {
    position: absolute;
    left: 352px; top: 96px;
    width: 2px; height: 196px;
    background: var(--accent);
  }
  .contact {
    position: absolute;
    left: 384px; top: 92px;
    color: var(--text);
  }
  .contact__name {
    color: var(--accent);
    font-size: 28px;
    font-weight: 600;
    letter-spacing: 1px;
  }
  .contact__role { font-size: 16px; margin: 2px 0 12px; }
  .contact__address { font-size: 16px; line-height: 1.4; margin-bottom: 8px; }
  .contact__line {
    display: flex;
    align-items: center;
    gap: 10px;
    font-size: 16px;
    line-height: 1.5;
  }
  .contact__line svg { width: 14px; height: 14px; flex: none; }
</style>
</head>
<body>
  <section class="card card--front" aria-label="Card front">
    <div class="brand">
      <span class="brand__dot"></span>
      <span class="brand__name">Tallow-Partners</span>
    </div>
  </section>

  <section class="card card--back" aria-label="Card back">
    <div class="brand">
      <span class="brand__dot"></span>
      <span class="brand__name">Tallow-Partners</span>
    </div>
    <div class="divider"></div>
    <div class="contact">
      <p class="contact__name">Dorian Whitlock</p>
      <p class="contact__role">Managing Director</p>
      <p class="contact__address">N ° 17/18 Rua Veloso<br>R / C 2B Direita<br>Bairro Mutamba - Luanda</p>
      <p class="contact__line">
        <svg viewBox="0 0 24 24" aria-hidden="true"><path fill="#29a3dc" d="M6.6 10.8a15 15 0 0 0 6.6 6.6l2.2-2.2a1 1 0 0 1 1-.25 11.4 11.4 0 0 0 3.6.6 1 1 0 0 1 1 1V20a1 1 0 0 1-1 1A17 17 0 0 1 3 4a1 1 0 0 1 1-1h3.5a1 1 0 0 1 1 1c0 1.25.2 2.45.6 3.6a1 1 0 0 1-.25 1z"/></svg>
        +244 947 582 316
      </p>
      <p class="contact__line">
        <svg viewBox="0 0 24 24" aria-hidden="true"><rect x="2.5" y="5" width="19" height="14" rx="1.5" fill="none" stroke="#29a3dc" stroke-width="2"/><path d="M3 6l9 7 9-7" fill="none" stroke="#29a3dc" stroke-width="2"/></svg>
        dorian.whitlock@tallow-p.example
      </p>
    </div>
  </section>
</body>
</html>
```